Business Card Design & Gift cards, Gift Cert, Donation Card

Retail Gift Store-in addition to Business Cards we'd like sequenced 2 sided Gift cards, Gift Certificate Cards, and Donation Cards.please see examples and email for clarificationlogos attached with examples-
Gift Card, Gift Certificate and Donation Card will all be same style just differant upper right title, with back side info as example.
business card, as example is single sided.
looking for additional ideas for layout

Industry/Entity Type

Business

Contact Information for Business Card

482 Larkfield Ave..East Tawas, MI 48730989.362.8730Office@BrewKrew.com

Requirements
Must have
• Blue as per example
• Logos provided
• like gradiant background

```html
<!DOCTYPE html>
<html lang="en">
<head>
<meta charset="utf-8">
<title>Tillow Marsh – Business Card &amp; Gift Certificate</title>
<link href="https://fonts.googleapis.com/css2?family=Kalam:wght@400;700&display=swap" rel="stylesheet">
<style>
  :root {
    --page-bg: #e4e4e4;
    --sky-top: #7dbcfb;
    --sky-bottom: #b5e2f5;
    --ink-blue: #1a2fb8;
    --ink-dark: #111111;
    --rule: #555555;
    --card-white: #ffffff;
    --art-red: #e20c05;
    --art-sun: #f5e20a;
    --art-faint-red: #f7c2c0;
    --art-faint-sun: #fbf4c4;
  }
  * { box-sizing: border-box; margin: 0; padding: 0; }
  html, body { width: 1189px; height: 1200px; overflow: hidden; }
  body {
    background: var(--page-bg);
    font-family: "Kalam", "Comic Sans MS", cursive;
    position: relative;
  }
  .card {
    position: absolute;
    left: 140px;
    width: 917px;
    height: 521px;
    box-shadow: 0 6px 14px rgba(0,0,0,.25);
  }
  .card--business {
    top: 46px;
    background: linear-gradient(to bottom, var(--sky-top), var(--sky-bottom));
  }
  .card--certificate { top: 600px; background: var(--card-white); }

  .mascot-art {
    position: absolute;
    left: 31px; top: 76px;
    width: 335px; height: 351px;
    border-radius: 40% 40% 8px 8px;
    background: linear-gradient(to bottom, var(--art-red) 0 70%, var(--art-sun) 70% 100%);
  }
  .brand-name {
    position: absolute;
    right: 49px; top: 84px;
    font-size: 74px;
    font-weight: 400;
    line-height: 1;
    color: var(--ink-blue);
    letter-spacing: 1px;
  }
  .address {
    position: absolute;
    right: 49px; top: 286px;
    text-align: right;
    font-size: 28px;
    line-height: 36px;
    color: var(--ink-dark);
    font-style: normal;
  }
  .offerings {
    position: absolute;
    right: 49px; top: 396px;
    text-align: right;
    font-size: 24px;
    line-height: 34px;
    color: var(--ink-dark);
  }

  .mascot-art--faint {
    left: 7px; top: 16px;
    width: 465px; height: 502px;
    background: linear-gradient(to bottom, var(--art-faint-red) 0 72%, var(--art-faint-sun) 72% 100%);
    opacity: .85;
  }
  .certificate-title {
    position: absolute;
    left: 264px; top: 100px;
    font-size: 48px;
    font-weight: 700;
    color: var(--ink-blue);
    letter-spacing: 2px;
    line-height: 1;
  }
  .field {
    position: absolute;
    display: flex;
    align-items: flex-end;
    font-size: 30px;
    line-height: 1;
    color: var(--ink-dark);
  }
  .field__line {
    flex: 1;
    border-bottom: 1.5px solid var(--rule);
    margin-left: 16px;
    height: 1px;
    margin-bottom: 4px;
  }
  .field--to     { left: 280px; top: 218px; width: 516px; }
  .field--from   { left: 280px; top: 273px; width: 516px; }
  .field--amount { left: 280px; top: 327px; width: 516px; }
  .field--small  { font-size: 27px; top: 449px; }
  .field--number     { left: 46px;  width: 264px; }
  .field--expiration { left: 322px; width: 323px; }
  .field--emp        { left: 663px; width: 207px; }
  .field--small .field__line { margin-left: 4px; }
</style>
</head>
<body>
  <section class="card card--business">
    <div class="mascot-art" role="img" aria-label="Illustration area: mascot figure stepping over a rising sun"></div>
    <h1 class="brand-name">TILLOW MARSH</h1>
    <address class="address">482 Larkfield Ave.<br>Pine Harbor, MI 48791</address>
    <p class="offerings">Gourmet Food, Fine Wines, Gift Baskets<br>Kitchen &amp; Bath Accessories, Candles, Cards, Soaps</p>
  </section>

  <section class="card card--certificate">
    <div class="mascot-art mascot-art--faint" role="img" aria-label="Faint background illustration of the mascot figure and sun"></div>
    <h2 class="certificate-title">GIFT CERTIFICATE</h2>
    <div class="field field--to"><span>TO:</span><span class="field__line"></span></div>
    <div class="field field--from"><span>FROM:</span><span class="field__line"></span></div>
    <div class="field field--amount"><span>AMOUNT:</span><span class="field__line"></span></div>
    <div class="field field--small field--number"><span>NUMBER</span><span class="field__line"></span></div>
    <div class="field field--small field--expiration"><span>EXPIRATION</span><span class="field__line"></span></div>
    <div class="field field--small field--emp"><span>EMP</span><span class="field__line"></span></div>
  </section>
</body>
</html>
```